tinyTally Resource Book - 10 maths tasks to do outside

I need a 22 (11 pages back to back) page A6 sized book produced to standard for submission to professional printer. Needs to be as .pdf file showing guide lines and allowances for colour bleed. I have text already written and submitted as attachment in a Word file with margins set to A6 size. The theme of the materials is "Nature Play" so using lots of pictures from nature (Australia preferably) and showing lots of patterns in nature (rocks, leaves, flower petals etc). Some of the tasks refer to specific activities, such as "shadows" and "floating" so would be great to illustrate appropriately. The big emphasis is on learning outside the classroom, getting kids to engage actively with nature. I would like to see the pages as full colour - so not white background. The book itself will be spiral bound along the top edge so a margin of at least 1cm will be required at the top of each page (or the bottom of even numbered pages). Book will be printed on plastic laminated matte paper for outdoor use. Font size needs to be big enough to read. Fonts sizes, alignments and page numbers are all different at the moment and need to be standardised. One photo is included in a page as a sample if you can use it, otherwise disregard. Logo for Wattlebrook Numeracy Guild is also included to have as part of the acknowledgements at the back of the book.

Target Market(s)

Book is for early childhood and preschool teachers.

Industry/Entity Type

Education

Font styles to use
Sans Serif

Requirements
Must have
• Colour and appeal.
Nice to have
• Use of natural colours instead of bright catchy colours but that is your call.
Should not have
• American spelling

```html
<!DOCTYPE html>
<html lang="en-AU">
<head>
<meta charset="utf-8">
<title>7. Make a Star</title>
<link rel="stylesheet" href="https://fonts.googleapis.com/css2?family=Jost:ital,wght@0,800;1,700&family=Didact+Gothic&display=swap">
<style>
  :root {
    --ink-blue: #2d3990;
    --accent-red: #d8252b;
    --body-ink: #2f2f2f;
    --paper: #ffffff;
    --trim: #3a3a3a;
    --stone-light: #d3c6b3;
    --stone-mid: #bcb0a0;
    --deck-grey: #a89d90;
  }
  html, body {
    margin: 0;
    padding: 0;
    width: 892px;
    height: 1200px;
    overflow: hidden;
    background: var(--paper);
  }
  .sheet {
    position: relative;
    width: 892px;
    height: 1200px;
    background: var(--paper);
    font-family: "Didact Gothic", "Century Gothic", sans-serif;
  }
  .trim-marks { position: absolute; inset: 0; }
  .nature-photo {
    position: absolute;
    left: 52px;
    top: 52px;
    width: 788px;
    height: 1096px;
    background: linear-gradient(160deg, var(--stone-light) 0%, var(--stone-mid) 45%, var(--deck-grey) 100%);
  }
  .page-text { position: absolute; inset: 0; }
  .task-title {
    position: absolute;
    top: 104px;
    left: 52px;
    width: 788px;
    margin: 0;
    text-align: center;
    font-family: "Jost", "Futura", sans-serif;
    font-weight: 800;
    font-size: 50px;
    line-height: 1;
    color: var(--ink-blue);
    text-shadow: 2px 2px 0 #fff, -1px -1px 0 #fff, 1px -1px 0 #fff, -1px 1px 0 #fff;
  }
  .outcome {
    position: absolute;
    top: 180px;
    left: 52px;
    width: 788px;
    margin: 0;
    text-align: center;
    font-family: "Jost", "Futura", sans-serif;
    font-weight: 800;
    font-size: 31px;
    line-height: 42px;
    color: var(--ink-blue);
    text-shadow: 2px 2px 0 #fff, -1px -1px 0 #fff, 1px -1px 0 #fff, -1px 1px 0 #fff;
  }
  .lead {
    position: absolute;
    left: 125px;
    margin: 0;
    white-space: nowrap;
    font-family: "Jost", "Futura", sans-serif;
    font-style: italic;
    font-weight: 700;
    font-size: 28px;
    line-height: 36px;
    color: var(--ink-blue);
  }
  .lead-dispositions { top: 284px; }
  .lead-educators { top: 520px; }
  .lead-task { top: 646px; }
  .statement {
    position: absolute;
    left: 196px;
    margin: 0;
    white-space: nowrap;
    font-size: 35px;
    letter-spacing: 0.6px;
    line-height: 45px;
    color: var(--body-ink);
  }
  .statement-play { top: 432px; }
  .statement-environment { top: 560px; }
  .opportunities {
    position: absolute;
    top: 685px;
    left: 194px;
    margin: 0;
    padding: 0;
    list-style: none;
    white-space: nowrap;
    font-size: 33px;
    letter-spacing: 0.5px;
    line-height: 42px;
    color: var(--body-ink);
  }
  .opportunities li {
    position: relative;
    padding-left: 24px;
  }
  .opportunities li::before {
    content: "";
    position: absolute;
    left: 3px;
    top: 13px;
    width: 16px;
    height: 16px;
    background: var(--accent-red);
    transform: rotate(45deg);
  }
  .page-number {
    position: absolute;
    left: 696px;
    top: 985px;
    width: 72px;
    height: 70px;
  }
  .page-number svg { position: absolute; inset: 0; }
  .page-number span {
    position: absolute;
    inset: 14px 0 0 0;
    text-align: center;
    font-size: 32px;
    line-height: 48px;
    color: #fff;
  }
</style>
</head>
<body>
<div class="sheet">
  <svg class="trim-marks" width="892" height="1200" aria-hidden="true">
    <g stroke="var(--trim)" stroke-width="0.8">
      <line x1="53" y1="0" x2="53" y2="36"/><line x1="74" y1="36" x2="74" y2="74"/>
      <line x1="0" y1="53" x2="36" y2="53"/><line x1="36" y1="74" x2="74" y2="74"/>
      <line x1="839" y1="0" x2="839" y2="36"/><line x1="818" y1="36" x2="818" y2="74"/>
      <line x1="856" y1="53" x2="892" y2="53"/><line x1="818" y1="74" x2="856" y2="74"/>
      <line x1="53" y1="1164" x2="53" y2="1200"/><line x1="74" y1="1126" x2="74" y2="1164"/>
      <line x1="0" y1="1147" x2="36" y2="1147"/><line x1="36" y1="1126" x2="74" y2="1126"/>
      <line x1="839" y1="1164" x2="839" y2="1200"/><line x1="818" y1="1126" x2="818" y2="1164"/>
      <line x1="856" y1="1147" x2="892" y2="1147"/><line x1="818" y1="1126" x2="856" y2="1126"/>
    </g>
  </svg>

  <div class="nature-photo" role="img" aria-label="Faded photograph of river stones arranged in a star shape on timber decking"></div>

  <div class="page-text">
    <h1 class="task-title">7. Make a Star</h1>
    <h2 class="outcome">EYLF – Outcome 4: Children are<br>confident and involved learners</h2>

    <p class="lead lead-dispositions">Children develop dispositions for learning such<br>as curiosity, cooperation, confidence, creativity,<br>commitment, enthusiasm, persistence, imagina-<br>tion and reflexivity when they...</p>
    <p class="statement statement-play">use play to investigate, imagine and<br>explore ideas</p>

    <p class="lead lead-educators">Educators promote this learning when they...</p>
    <p class="statement statement-environment">provide learning environments that<br>are flexible and open-ended</p>

    <p class="lead lead-task">This task provides an opportunity to:</p>
    <ul class="opportunities">
      <li>explore the concept of<br>“alternating turns”</li>
      <li>share and cooperate<br>to produce a star</li>
      <li>explore concept of<br>repeated addition</li>
      <li>develop awareness<br>of radial symmetry</li>
    </ul>

    <div class="page-number">
      <svg width="72" height="70" viewBox="0 0 72 70" aria-hidden="true">
        <polygon points="36,0 72,26 58,70 14,70 0,26" fill="var(--ink-blue)"/>
      </svg>
      <span>14</span>
    </div>
  </div>
</div>
</body>
</html>
```